Business Card (double-sided) and Stationary Design for dental office

1) Business Card Design: We need a business card design for a dental specialty office.
Texts should contain:
The name of our office "Brindle Oaks Orthodontics"
Tagline: "Specialist in Orthodontic and Maxillofacial Orthopedics"
Tag line: "Creating "Tolvering" smiles for Children and Adults"
Doctor name: "Doctor Name"
Office Address:
"123 Street Name
City, State Zip code"
Office email address: office@brindleoaksortho.com
Website: www.brindleoaksortho.com

We will provide the full office address once the design is selected
Theme: beach, paradise, coastal, wave
We would like to have some creativity in design. Some acceptable ideas: front page: logo and office name. Back page: more detail information, and map to office in form of an island. Please see sample from our other location, but you DON'T HAVE TO USE OR COPY THE SAME CONCEPT.

IF POSSIBLE, PLEASE SUBMIT AT LEAST TWO CONCEPTS: ONE WITH THE BACK LOOKING SIMILAR TO WHAT IS IN THE SAMPLE, AND ONE DIFFERENT.

Color: designer to choose. We have different shade of blues and sand color in our office. Please see logo.

2) Please also design a matching set of stationary that compliment the business card and our logo.

Target Market(s)

Dental

Contact Information for Business Card

See descriptions

Font styles to use
Other font styles liked:
• Matching texts in logo

Colors
0054AA
0677BA
7BADD7
CADEEF
E8F1F8
0094D4
00A9DD
6FCCEA
C7EBF8
E9F6FB
00AB8E
00BBA5
67D7C9
C6EFE9
E9F9F6

Requirements
Must have
• Double-sided
Nice to have
• Beach coastal theme
Should not have
• Any shape or drawing of of tooth or teeth. We don’t need these. You don't necessarily have to just cut and paste the logo art and text as a whole, you have the liberty to rearrange the text.

```html
<!DOCTYPE html>
<html lang="en">
<head>
<meta charset="utf-8">
<title>Brindle Oaks Orthodontics – Stationery Set</title>
<link rel="stylesheet" href="https://fonts.googleapis.com/css2?family=Ubuntu:ital,wght@0,400;0,500;0,700;1,700&family=Comic+Neue:wght@700&display=swap">
<style>
:root{
  --backdrop:#8f8d8e;
  --paper:#f4f3f4;
  --paper-edge:#e4e3e5;
  --teal:#2f869e;
  --teal-dark:#287590;
  --mint:#7cc5b2;
  --brand:#2e8ba3;
  --brand-sub:#3fb5a4;
  --ink:#4a4a4a;
  --ink-soft:#6b6b6b;
  --faint:rgba(46,139,163,.08);
  --sign-red:#8a1e12;
}
*{box-sizing:border-box;margin:0;padding:0}
html,body{width:1200px;height:826px;overflow:hidden}
body{background:var(--backdrop);position:relative;font-family:"Ubuntu",sans-serif;color:var(--ink)}
.sheet{position:absolute;background:linear-gradient(90deg,var(--paper),#fafafa 60%,var(--paper));box-shadow:0 1px 4px rgba(0,0,0,.3);overflow:hidden}
.mark{position:absolute;border-radius:50%;border:3px solid var(--brand);background:#fff}
.mark--light{border-color:#fff;background:transparent}
.watermark{position:absolute;border-radius:50%;background:var(--faint)}
.brand-name{position:absolute;font-weight:500;color:var(--brand);white-space:nowrap;letter-spacing:.2px}
.brand-tag{position:absolute;color:var(--brand-sub);white-space:nowrap;letter-spacing:.6px}
.band{position:absolute;left:0;right:0;background:linear-gradient(90deg,var(--teal) 0,var(--teal) 87%,var(--mint) 87%)}
.band-text{position:absolute;color:#fff;font-size:9px;line-height:11.5px;letter-spacing:.2px}

/* letterhead */
.letterhead{left:60px;top:111px;width:461px;height:645px}
.letterhead .mark{left:208px;top:34px;width:46px;height:46px}
.letterhead .brand-name{left:0;right:0;top:80px;text-align:center;font-size:17px}
.letterhead .brand-tag{left:0;right:0;top:98px;text-align:center;font-size:5.5px}
.letterhead .watermark{left:130px;top:205px;width:212px;height:212px}
.letter-body{position:absolute;left:41px;top:188px;width:386px}
.salutation{font-size:12px;color:var(--ink);margin-bottom:18px}
.letter-body p{font-size:6.4px;line-height:10px;color:var(--ink-soft);margin-bottom:8px;text-align:justify}
.letter-body .closing{margin-top:20px}
.letterhead .band{top:582px;height:31px}
.letterhead .band-text{left:42px;top:4px}
.letterhead .band .mark{left:387px;top:1px;width:29px;height:29px;border-width:2px}

/* business card front */
.card{top:120px;width:289px;height:164px}
.card-front{left:550px}
.card-front .band{top:27px;height:28px;background:linear-gradient(90deg,var(--teal) 0,var(--teal) 78%,var(--mint) 78%)}
.holder{position:absolute;left:25px;top:7px;font-family:"Comic Neue",sans-serif;font-size:11.5px;color:#fff;letter-spacing:.5px}
.card-front .mark{left:191px;top:20px;width:42px;height:42px;border-width:3px}
.card-front .brand-name{left:130px;width:166px;text-align:center;top:63px;font-size:12.5px}
.card-front .brand-tag{left:130px;width:166px;text-align:center;top:78px;font-size:4px}
.card-front .watermark{left:-15px;top:80px;width:100px;height:100px}
.contact{position:absolute;left:26px;top:117px;font-size:6.8px;line-height:8.6px;color:var(--ink)}
.contact li{list-style:none;display:flex;align-items:center;gap:4px}
.contact svg{width:6px;height:6px;fill:var(--teal)}
.office{position:absolute;right:28px;top:117px;text-align:right;font-size:6.8px;line-height:8.6px;color:var(--ink)}

/* business card back */
.card-back{left:862px}
.island-scene{position:absolute;inset:0;background:linear-gradient(180deg,#4fb4e6 0,#9ad8f3 30%,#2fa6d8 48%,#f3c15a 62%,#e7a53d 100%)}
.card-back .mark{left:126px;top:20px;width:32px;height:32px;border-width:3px;border-color:#4a2a1a}
.card-back .brand-name{left:0;width:180px;text-align:center;top:55px;font-size:10px;color:#3a2a20;font-weight:700}
.card-back .brand-tag{left:0;width:180px;text-align:center;top:67px;font-size:3.5px;color:#3a2a20}
.appointment{position:absolute;left:12px;top:75px;width:181px;height:49px;background:rgba(255,255,255,.85);border-radius:3px;padding:5px 8px;font-size:6px;color:#222}
.appointment strong{display:block;font-size:6.3px;margin-bottom:5px}
.field{display:flex;align-items:flex-end;gap:2px;margin-bottom:5px}
.field span.line{flex:1;border-bottom:.6px dotted #555;height:6px}
.specialty{position:absolute;left:0;width:180px;text-align:center;top:138px;font-size:6.2px;line-height:8px;color:var(--sign-red);font-weight:700;font-style:italic}

/* envelopes */
.envelope-back{left:602px;top:337px;width:529px;height:240px}
.flap{position:absolute;left:0;top:0;width:529px;height:75px}
.envelope-back .mark{left:240px;top:15px;width:44px;height:44px}
.envelope-front{left:565px;top:511px;width:530px;height:241px}
.envelope-front .mark{left:64px;top:26px;width:47px;height:47px}
.envelope-front .brand-name{left:26px;width:128px;text-align:center;top:76px;font-size:16px}
.envelope-front .brand-tag{left:26px;width:128px;text-align:center;top:93px;font-size:5.3px}
.envelope-front .watermark{left:313px;top:90px;width:187px;height:187px}
.envelope-front .band{top:183px;height:31px}
.envelope-front .band-text{left:25px;top:4px}
.envelope-front .band .mark{left:452px;top:1px;width:29px;height:29px;border-width:2px}
</style>
</head>
<body>

<section class="sheet letterhead" aria-label="Letterhead">
  <span class="mark"></span>
  <div class="brand-name">BrindleOaks</div>
  <div class="brand-tag">Pediatric Dentistry &amp; Orthodontics</div>
  <span class="watermark"></span>
  <div class="letter-body">
    <p class="salutation">Dear Mr. Ferro,</p>
    <p>Lorem ipsum dolor sit amet, consectetur adipiscing elit. Donec orci purus, luctus vitae dignissim eu, iaculis sed purus. Vivamus faucibus, ipsum nec aliquet viverra, leo mauris condimentum ligula, sit amet sagittis enim ligula quis arcu. Nam egestas tortor id nisi porttitor mattis. In tortor ante, ultricies in suscipit a, tempus non massa. Vivamus et auctor mi. Fusce vel massa nulla. Phasellus nec eros mauris, et scelerisque orci.</p>
    <p>Donec malesuada orci vitae nulla accumsan porta a id massa. Quisque accumsan iaculis magna sit amet fringilla. Maecenas consequat, magna eget tincidunt semper, odio nibh rutrum mi, id feugiat ante nisi eu risus. Vestibulum nunc orci, rhoncus a placerat in, ultricies in mi. Cras mattis varius eros, vel fringilla nisi suscipit eget. Quisque scelerisque sagittis nulla at porttitor.</p>
    <p>Sed id augue vitae urna euismod commodo aliquet a quam. Pellentesque arcu velit, cursus et malesuada ut, consequat et diam. Nullam erat sem, rhoncus id ullamcorper vitae, rhoncus et arcu. In ultricies ultricies nulla, ut rutrum nisi iaculis at. Donec eu magna a metus ornare faucibus. Fusce aliquet faucibus ultricies. Morbi semper, est id tincidunt gravida, sem arcu adipiscing lacus, ac bibendum nulla leo eu purus. Quisque nec diam sed risus consectetur accumsan quis quis nibh. Vestibulum id purus lorem.</p>
    <p>It is a long established fact that a reader will be distracted by the readable content of a page when looking at its layout. The point of using Lorem Ipsum is that it has a more-or-less normal distribution of letters, as opposed to using 'Content here, content here', making it look like readable English. Many desktop publishing packages</p>
    <p class="closing">Sincerely,</p>
  </div>
  <div class="band">
    <div class="band-text">Brindle Oaks Dentistry 123 Street Name, City, State Zip code<br>P. 555-014-2760 E. office@brindleoaksortho.com W. brindleoaksortho.com</div>
    <span class="mark mark--light"></span>
  </div>
</section>

<section class="sheet card card-front" aria-label="Business card front">
  <span class="watermark"></span>
  <div class="band"><span class="holder">Daniel Ferro</span></div>
  <span class="mark"></span>
  <div class="brand-name">BrindleOaks</div>
  <div class="brand-tag">Pediatric Dentistry &amp; Orthodontics</div>
  <ul class="contact">
    <li><svg viewBox="0 0 10 10"><path d="M2 0l2 2-1 2c1 1 2 2 3 3l2-1 2 2-2 2C4 9 1 6 0 2z"/></svg>555-014-2760</li>
    <li><svg viewBox="0 0 10 10"><path d="M0 2h10v6H0zM0 2l5 3 5-3" /></svg>office@brindleoaksortho.com</li>
    <li><svg viewBox="0 0 10 10"><circle cx="5" cy="5" r="5"/></svg>brindleoaksortho.com</li>
  </ul>
  <div class="office">Brindle Oaks Dentistry<br>123 Street Name<br>City, State Zip code</div>
</section>

<section class="sheet card card-back" aria-label="Business card back">
  <div class="island-scene" role="img" aria-label="Illustrated tropical beach with palm trees, rock and an island map to the office"></div>
  <span class="mark"></span>
  <div class="brand-name">BrindleOaks</div>
  <div class="brand-tag">Pediatric Dentistry &amp; Orthodontics</div>
  <div class="appointment">
    <strong>SEE YOU AT YOUR NEXT APPOINTMENT!</strong>
    <div class="field">For<span class="line"></span></div>
    <div class="field">Date<span class="line"></span>Time<span class="line"></span></div>
  </div>
  <div class="specialty">Specialist in Orthodontic &amp; Maxillofacial Orthopedics<br>Creating "Tolvering" smiles for Children &amp; Adults</div>
</section>

<section class="sheet envelope-back" aria-label="Envelope back">
  <svg class="flap" viewBox="0 0 529 75" preserveAspectRatio="none" aria-hidden="true">
    <path d="M0 0H529V52Q529 75 506 75H23Q0 75 0 52Z" fill="var(--teal)"/>
  </svg>
  <span class="mark mark--light"></span>
</section>

<section class="sheet envelope-front" aria-label="Envelope front">
  <span class="watermark"></span>
  <span class="mark"></span>
  <div class="brand-name">BrindleOaks</div>
  <div class="brand-tag">Pediatric Dentistry &amp; Orthodontics</div>
  <div class="band">
    <div class="band-text">Brindle Oaks Dentistry<br>123 Street Name, City, State Zip code</div>
    <span class="mark mark--light"></span>
  </div>
</section>

</body>
</html>
```